Business card design for holistic health care clinic

We need a double-sided business card design for our holistic health care clinic that integrates our logo design and also its color scheme. My business is called Valmira. It is an integrative medicine clinic. You have already done the logo for me. Please ensure an elegant and upscale design that is not cluttered, but still has all the necessary information (please see below for details).

Target Market(s)

Wellness, fitness, rehabilitation for educated, well-traveled open-minded clients who are focused on natural, organic, balanced and preventive healthcare and lifestyle.

Industry/Entity Type

Medical

Contact Information for Business Card

Modern, clean.

Number of Pages Required

1 page

Font styles to use
Serif
Sans Serif

Colors

Designer to choose colors to be used in the design.

Requirements
Must have
• Logo on one side, all other information on the other side.
• Other information should include:
• Tobias Wrenfeld - DOE, CPT, LMT
• 4100 East Marrow Drive
• Austin, TX 78119
• 512 555 0148
• 818 555 0192
• info@ValmiraHealth.example
• t.wrenfeld@ValmiraHealth.example
Nice to have
• Darker background on front - but not totally black - shaded/dark gray.

```html
<!DOCTYPE html>
<html lang="en">
<head>
<meta charset="utf-8">
<title>Valmira – Business Card</title>
<link rel="stylesheet" href="https://fonts.googleapis.com/css2?family=Nunito:wght@800&family=Roboto:ital,wght@0,400;1,400&family=Roboto+Condensed:wght@700&display=swap">
<style>
  :root {
    --stage: #2c2c2c;
    --card-white: #f6f6f6;
    --card-dark: #2a2a2b;
    --brand-blue: #0b8fd0;
    --text-grey: #444444;
    --rule-grey: #8a8a8a;
  }
  html, body {
    margin: 0;
    width: 1200px;
    height: 960px;
    overflow: hidden;
    background: var(--stage);
  }
  .canvas {
    position: relative;
    width: 1200px;
    height: 960px;
  }
  .card {
    position: absolute;
    left: 320px;
    width: 600px;
    border-radius: 22px;
    overflow: hidden;
    background: var(--card-white);
  }
  .card--front { top: 93px; height: 357px; }
  .card--back  { top: 493px; height: 342px; background: #ffffff; }

  .brand-name {
    font-family: "Nunito", sans-serif;
    font-weight: 800;
    color: var(--brand-blue);
    letter-spacing: 1px;
    margin: 0;
    line-height: 1;
  }
  .card--front .brand-name {
    position: absolute;
    top: 160px;
    left: 0;
    right: 0;
    text-align: center;
    font-size: 70px;
  }
  .tagline {
    position: absolute;
    top: 287px;
    left: 90px;
    right: 90px;
    display: flex;
    align-items: center;
    gap: 8px;
    font-family: "Roboto", sans-serif;
    font-style: italic;
    font-size: 17px;
    color: var(--text-grey);
    white-space: nowrap;
  }
  .tagline::before, .tagline::after {
    content: "";
    flex: 1;
    height: 1px;
    background: linear-gradient(90deg, transparent, var(--rule-grey));
  }
  .tagline::after { background: linear-gradient(90deg, var(--rule-grey), transparent); }

  .back-art { position: absolute; inset: 0; }
  .card--back .brand-name {
    position: absolute;
    top: 62px;
    left: 34px;
    font-size: 44px;
  }
  .contact {
    position: absolute;
    right: 25px;
    top: 145px;
    font-family: "Roboto", sans-serif;
    font-size: 15px;
    color: var(--text-grey);
    text-align: right;
    line-height: 19.3px;
  }
  .contact__row {
    display: flex;
    justify-content: flex-end;
    align-items: center;
    gap: 8px;
  }
  .contact__icon { width: 13px; height: 13px; fill: var(--brand-blue); }
  .contact__address { margin-top: 5px; padding-right: 0; }
  .holder {
    position: absolute;
    right: 25px;
    top: 290px;
    font-family: "Roboto Condensed", sans-serif;
    font-weight: 700;
    color: var(--brand-blue);
    font-size: 22px;
    text-transform: uppercase;
    margin: 0;
  }
  .holder__credentials { font-size: 14px; }
</style>
</head>
<body>
<main class="canvas">
  <section class="card card--front" aria-label="Card front">
    <h1 class="brand-name">VALMIRA</h1>
    <p class="tagline">helping the body help itself</p>
  </section>

  <section class="card card--back" aria-label="Card back">
    <svg class="back-art" width="600" height="342" viewBox="0 0 600 342" aria-hidden="true">
      <path d="M0 0 H400 C390 140 300 250 95 342 H0 Z" fill="var(--brand-blue)"/>
      <path d="M0 0 H375 C365 130 275 240 65 342 H0 Z" fill="var(--card-dark)"/>
    </svg>
    <h2 class="brand-name">VALMIRA</h2>
    <div class="contact">
      <div class="contact__row">512 555 0148
        <svg class="contact__icon" viewBox="0 0 16 16"><path d="M3.5 1 6 4 4.6 5.8c.9 2 2.6 3.7 4.6 4.6L11 9l3 2.5-1.3 2.8C7 14 2 9 1.7 3.2Z"/></svg></div>
      <div class="contact__row">818 555 0192
        <svg class="contact__icon" viewBox="0 0 16 16"><path d="M4 1h8v14H4Zm1.5 1.5v9h5v-9ZM8 12.3a.9.9 0 1 0 0 1.8.9.9 0 0 0 0-1.8Z"/></svg></div>
      <div class="contact__row">t.wrenfeld@ValmiraHealth.example
        <svg class="contact__icon" viewBox="0 0 16 16"><path d="M1 3.5h14v9H1Zm1.5 1 5.5 4 5.5-4Z"/></svg></div>
      <div class="contact__row">www.ValmiraHealth.example
        <svg class="contact__icon" viewBox="0 0 16 16"><circle cx="8" cy="8" r="7"/></svg></div>
      <div class="contact__address">4100 East Marrow Drive<br>Austin, TX 78119</div>
    </div>
    <p class="holder">Tobias Wrenfeld <span class="holder__credentials">- DOE, CPT, LMT</span></p>
  </section>
</main>
</body>
</html>
```